Law Firm Business Card

This is a business card for a law firm that serves US military and veterans.

The card must have ONLY the following (we want an uncluttered look):

- Company logo (PNG, GIF, JPEG copies uploaded)
- A tagline reading: "a law firm for service members and veterans"
- My name and title: "Tobias Marlow" and "Attorney"
- My email: "tobias.marlow@brinmoorlegal.com"
- My number: "855-FIRM-ONE (347-6663)"

We are looking for a clean, simple layout with only the above information, likely printed on a bright white cotton stock. The font of our logo is DIN 1451, and the font used on our website is Helvetica Neue. The color of our logo is #336699, and we probably want the tagline in that color also, and my contact information in a dark grey. Please review our website at www.brinmoorlegal.com to ensure your card design complements our website style.

Thanks and we look forward to seeing your submissions.

A few notes:

- Two-sided submissions are ok
- Please don't add graphics (scales of justice, judges hammer, etc)

```html
<!DOCTYPE html>
<html lang="en">
<head>
<meta charset="utf-8">
<title>Brinmoor Legal – Business Card</title>
<link rel="stylesheet" href="https://fonts.googleapis.com/css2?family=Barlow+Semi+Condensed:wght@600&family=Crimson+Text:ital,wght@0,400;1,600&display=swap">
<style>
  :root {
    --brand-blue: #336699;
    --accent-blue: #3a6fc4;
    --ink-grey: #3a3f47;
    --card-white: #f4f6f8;
    --backdrop: #e3e5e8;
    --rule: #5b7fb3;
  }
  * { box-sizing: border-box; margin: 0; padding: 0; }
  html, body {
    width: 1200px; height: 501px; overflow: hidden;
    background: var(--backdrop);
  }
  .sheet {
    position: relative; width: 1200px; height: 501px;
    display: flex; justify-content: center; align-items: center; gap: 40px;
  }
  .card {
    position: relative; width: 500px; height: 290px;
    padding: 0 40px;
    background: var(--card-white);
    border-radius: 26px;
    box-shadow: 0 6px 18px rgba(0,0,0,.18);
    overflow: hidden;
    display: flex; flex-direction: column; align-items: center;
  }
  .card__edge {
    position: absolute; top: 40px; bottom: 40px; width: 6px;
    background: var(--accent-blue); border-radius: 3px;
  }
  .card__edge--left { left: 6px; }
  .card__edge--right { right: 6px; }

  .wordmark {
    font-family: "Barlow Semi Condensed", "Arial Narrow", sans-serif;
    font-weight: 600; color: var(--accent-blue);
    text-transform: uppercase; letter-spacing: 2px; line-height: 1;
    white-space: nowrap; text-align: center;
  }
  .card--front .wordmark { font-size: 42px; margin-top: 50px; }
  .card--back { justify-content: center; }
  .card--back .wordmark { font-size: 52px; }

  .tagline {
    font-family: "Crimson Text", Georgia, serif;
    color: var(--brand-blue); font-size: 17px; margin-top: 18px;
    white-space: nowrap;
  }
  .holder {
    font-family: "Crimson Text", Georgia, serif;
    font-size: 19px; color: var(--brand-blue); margin-top: 16px;
    padding: 0 30px 6px; border-bottom: 1.5px solid var(--rule);
  }
  .holder__name { font-style: italic; font-weight: 600; }
  .contact {
    list-style: none; margin-top: 10px;
    font-family: "Crimson Text", Georgia, serif;
    font-size: 16px; color: var(--ink-grey);
  }
  .contact__item { display: flex; align-items: center; gap: 7px; line-height: 1.45; }
  .contact__icon { width: 13px; height: 13px; fill: var(--ink-grey); }
</style>
</head>
<body>
<main class="sheet">
  <section class="card card--front" aria-label="Card front">
    <span class="card__edge card__edge--left"></span>
    <span class="card__edge card__edge--right"></span>
    <h1 class="wordmark">Brinmoor Legal</h1>
    <p class="tagline">A Law Firm For Service Members And Veterans</p>
    <p class="holder"><span class="holder__name">Tobias Marlow</span>, Attorney</p>
    <ul class="contact">
      <li class="contact__item">
        <svg class="contact__icon" viewBox="0 0 24 24" aria-hidden="true"><path d="M6.6 10.8a15 15 0 0 0 6.6 6.6l2.2-2.2a1 1 0 0 1 1-.25 11.4 11.4 0 0 0 3.6.57 1 1 0 0 1 1 1V20a1 1 0 0 1-1 1A17 17 0 0 1 3 4a1 1 0 0 1 1-1h3.5a1 1 0 0 1 1 1c0 1.25.2 2.45.57 3.57a1 1 0 0 1-.25 1z"/></svg>
        855-FIRM-ONE (347-6663)
      </li>
      <li class="contact__item">
        <svg class="contact__icon" viewBox="0 0 24 24" aria-hidden="true"><path d="M3 5h18a1 1 0 0 1 1 1v12a1 1 0 0 1-1 1H3a1 1 0 0 1-1-1V6a1 1 0 0 1 1-1zm1 2.2V17h16V7.2l-8 5.3z M4.5 7l7.5 5 7.5-5z"/></svg>
        tobias.marlow@brinmoorlegal.com
      </li>
    </ul>
  </section>

  <section class="card card--back" aria-label="Card back">
    <h2 class="wordmark">Brinmoor Legal</h2>
  </section>
</main>
</body>
</html>
```